Stationary Set Rebrand for Brennick

We are a Canadian Distribution and Service Company that was established in 1969. Over the past 5 decades we have expanded our business and have warehouses across Canada. We specialize in adhesive tapes, adhesives, films, safety, warehouse, shipping, janitorial and packaging supplies.

We have updated our logo design and would like a new corporate branding identity that includes a new fresh Stationary Set (Business Cards, Letterhead, Letterhead MS Word, Envelope, Presentation Folders, Email Signatures, Notepad Covers, etc.)

Target Market(s)

Industrial Business Sector

Font styles to use
Sans Serif

Colors
0054AA
0677BA
7BADD7
CADEEF
E8F1F8
0094D4
00A9DD
6FCCEA
C7EBF8
E9F6FB
00AB8E
00BBA5
67D7C9
C6EFE9
E9F9F6
EB3D1F
EC4F4E
F09395
F8D3D4
FCEDEE

Requirements
Should not have
• Colors not too light, darker colours preferred

```html
<!DOCTYPE html>
<html lang="en">
<head>
<meta charset="utf-8">
<title>Brennick Business Card</title>
<link rel="stylesheet" href="https://fonts.googleapis.com/css2?family=Archivo:wdth,wght@125,800&family=Saira:wght@400;700&display=swap">
<style>
  :root {
    --bg: #dedede;
    --red: #d71920;
    --ink: #231f20;
    --charcoal: #303030;
    --white: #ffffff;
  }
  * { margin: 0; padding: 0; box-sizing: border-box; }
  html, body { width: 1200px; height: 1200px; overflow: hidden; }
  body { background: var(--bg); position: relative; font-family: "Saira", sans-serif; }

  .card { position: absolute; overflow: hidden; }

  /* Front */
  .card-front { left: 262px; top: 156px; width: 696px; height: 398px;
    background: linear-gradient(to bottom, var(--white) 0 284px, var(--ink) 284px 100%); }
  .front-panel { position: absolute; left: 26px; top: 27px; width: 644px; height: 345px; background: var(--red); }
  .person-name { position: absolute; left: 53px; top: 51px; font-family: "Archivo", sans-serif;
    font-stretch: 125%; font-weight: 800; font-size: 22px; letter-spacing: 0.5px; color: var(--ink); line-height: 1; }
  .person-title { position: absolute; left: 52px; top: 76px; font-size: 15.5px; color: var(--white); letter-spacing: 0.4px; }
  .address { position: absolute; left: 53px; top: 154px; font-size: 16.5px; line-height: 21px; color: var(--white); letter-spacing: 0.6px; }
  .contacts { position: absolute; left: 52px; top: 213px; list-style: none; }
  .contacts li { display: flex; align-items: center; height: 21px; font-size: 16.5px; color: var(--white); letter-spacing: 0.6px; }
  .contacts svg { width: 14px; height: 14px; margin-right: 13px; fill: var(--ink); }
  .front-brand { position: absolute; left: 346px; top: 224px; font-weight: 700; font-size: 52px;
    line-height: 1; color: var(--ink); }

  /* Back */
  .card-back { left: 258px; top: 651px; width: 695px; height: 397px;
    background: linear-gradient(to bottom, var(--charcoal) 0 283px, var(--red) 283px 100%); }
  .back-panel { position: absolute; left: 25px; top: 28px; width: 643px; height: 344px; background: var(--white);
    display: flex; align-items: center; justify-content: center; }
  .back-brand { font-weight: 700; font-size: 84px; line-height: 1; color: var(--ink); }
</style>
</head>
<body>
  <section class="card card-front">
    <div class="front-panel">
      <h1 class="person-name">ALAN MARSH</h1>
      <p class="person-title">President</p>
      <p class="address">4152 Cedarfield Road<br>Thunder Bay, Canada 28419</p>
      <ul class="contacts">
        <li><svg viewBox="0 0 24 24"><path d="M6.6 10.8a15 15 0 0 0 6.6 6.6l2.2-2.2a1 1 0 0 1 1-.25 11.4 11.4 0 0 0 3.6.57 1 1 0 0 1 1 1V20a1 1 0 0 1-1 1A17 17 0 0 1 3 4a1 1 0 0 1 1-1h3.5a1 1 0 0 1 1 1c0 1.25.2 2.45.57 3.57a1 1 0 0 1-.25 1z"/></svg>555-214-8830</li>
        <li><svg viewBox="0 0 24 24"><path d="M7 1h10a2 2 0 0 1 2 2v18a2 2 0 0 1-2 2H7a2 2 0 0 1-2-2V3a2 2 0 0 1 2-2zm0 3v15h10V4z"/></svg>555-367-1492</li>
        <li><svg viewBox="0 0 24 24"><path d="M2 5h20v14H2zm2 2v.5l8 5 8-5V7zm0 3v7h16v-7l-8 5z"/></svg>info@brennick.com</li>
        <li><svg viewBox="0 0 24 24"><circle cx="12" cy="12" r="10"/></svg>www.brennick.com</li>
      </ul>
      <div class="front-brand">Brennick</div>
    </div>
  </section>

  <section class="card card-back">
    <div class="back-panel">
      <div class="back-brand">Brennick</div>
    </div>
  </section>
</body>
</html>
```